Mortgage Company Flyer (About Us, Key Strengths, Contact Info)

We are trying to make a mortgage company flyer that is simple, modern, and explains who we are, what we do best, and how to get in touch with us.
There will be two people listed on the flyer, a loan officer and a spanish speaking loan officer assistant
We will also have a QR code directed to an application link
As far as the key strengths, we want to put
*Low rates and closing cost
*Fast Underwrite - 24 Hours or Less
*Responsive, Professional, and Experienced
*Hundreds of products for borrowers who have been declined
Logos attached and sample flyers from competitors attached.
People on flyer - Carla Wendt (Loan Officer)
Rosa Medina - Spanish Speaking Loan Officer Assistant (Indicate "Se Habla Espanol")
What is the goal of this flyer? We need an easy way/summary for real estate agents to get in touch with our team and know who to call and what we are strong in.

```html
<!DOCTYPE html>
<html lang="en">
<head>
<meta charset="utf-8">
<title>BrightKey Lending Flyer</title>
<link rel="stylesheet" href="https://fonts.googleapis.com/css2?family=Poppins:wght@400;500;600;700&display=swap">
<style>
:root{
  --navy:#1b4f72;
  --navy-deep:#153f5e;
  --green:#8cbf3a;
  --green-strong:#7cb132;
  --lime:#b9d95a;
  --lime-soft:#c4de6e;
  --row-grey:#e2e7eb;
  --ink:#1d3550;
  --white:#ffffff;
  --page:#eef1f3;
}
*{margin:0;padding:0;box-sizing:border-box}
html,body{width:1200px;height:2400px;overflow:hidden}
body{background:var(--page);font-family:"Poppins",sans-serif;color:var(--ink);position:relative}
.flyer{position:absolute;left:40px;top:475px;width:1120px;height:1450px;background:var(--white);overflow:hidden;box-shadow:0 20px 40px rgba(0,0,0,.18)}
.hero-band{position:absolute;left:0;top:0;width:1120px;height:681px;background:linear-gradient(135deg,#1d5577,#184868)}
.brand{position:absolute;left:55px;top:118px;display:flex;align-items:center;gap:12px;color:var(--white);font-weight:600;font-size:36px}
.brand-mark{width:30px;height:30px;background:var(--green)}
.headline{position:absolute;left:55px;top:262px;color:var(--white);line-height:1.05}
.headline .light{display:block;font-weight:400;font-size:56px}
.headline .bold{display:block;font-weight:700;font-size:56px}
.headline .accent{display:block;font-weight:700;font-size:78px;color:var(--lime);margin-top:4px}
.divider{position:absolute;left:0;top:478px;width:258px;height:3px;background:var(--green)}
.intro{position:absolute;left:55px;top:496px;width:470px;color:var(--white);font-size:30px;font-weight:500;line-height:1.25}
.intro strong{font-weight:700}
.photo-back{position:absolute;left:545px;top:78px;width:520px;height:500px;background:var(--green);border-radius:24px 120px 24px 60px}
.photo-frame{position:absolute;left:567px;top:62px;width:496px;height:494px;background:var(--white);border-radius:20px 110px 20px 60px;padding:9px}
.photo{width:100%;height:100%;border-radius:14px 102px 14px 54px;background:linear-gradient(180deg,#dfe8ee 0%,#c9ccc8 45%,#8e8a82 100%)}
.strengths{position:absolute;left:52px;top:623px;width:1012px;height:96px;display:flex;border-radius:12px;overflow:hidden}
.strength{display:flex;align-items:center;gap:14px;padding-left:28px;color:var(--ink);font-weight:600;font-size:26px;background:var(--green)}
.strength:nth-child(1){width:303px}
.strength:nth-child(2){width:363px;background:var(--lime-soft);border-left:2px solid var(--white);border-right:2px solid var(--white)}
.strength:nth-child(3){flex:1}
.badge{width:58px;height:58px;border-radius:50%;background:var(--white);display:flex;align-items:center;justify-content:center;flex-shrink:0}
.showcase{position:absolute;left:0;top:740px;width:420px;height:290px;background:linear-gradient(160deg,#f3f4f5 0%,#d7d9dc 55%,#5b6066 100%);border-radius:0 40px 40px 0}
.features{position:absolute;left:468px;top:740px;width:596px}
.feature{position:relative;height:66px;margin-bottom:25px;display:flex;align-items:center}
.feature-bar{position:absolute;left:33px;right:0;top:0;bottom:0;background:var(--row-grey);border-radius:0 8px 8px 0}
.feature.primary .feature-bar{background:var(--green-strong)}
.feature-icon{position:relative;width:70px;height:70px;border-radius:50%;background:var(--navy);border:5px solid #d5dde3;display:flex;align-items:center;justify-content:center;flex-shrink:0}
.feature-text{position:relative;margin-left:22px;font-size:23px;font-weight:500;line-height:1.1;color:var(--ink)}
.feature.primary .feature-text{color:var(--white);font-weight:600;font-size:25px}
.person{position:absolute;top:1028px;height:151px;background:var(--navy);border-radius:8px;color:var(--white)}
.person.officer{left:61px;width:445px}
.person.assistant{left:567px;width:497px;background:var(--navy-deep)}
.portrait{position:absolute;top:-18px;left:0;width:198px;height:198px;border-radius:50%;border:6px solid var(--green);background:linear-gradient(180deg,#c9a98f,#6d5548)}
.person-info{position:absolute;left:218px;top:50%;transform:translateY(-50%);line-height:1.12}
.person-name{font-weight:700;font-size:27px;text-transform:uppercase}
.person-role{font-size:20px;text-transform:uppercase}
.person-note{font-size:23px;font-weight:700;color:var(--lime);text-transform:uppercase}
.contact{position:absolute;left:61px;top:1223px;width:1001px;height:166px;background:var(--lime);border-radius:24px 24px 24px 40px}
.contact-tab{position:absolute;left:0;top:0;width:870px;height:56px;background:var(--navy);border-radius:24px 0 14px 0;color:var(--white);font-weight:700;font-size:28px;display:flex;align-items:center;padding-left:27px}
.contact-tab span{color:var(--lime);margin-left:8px}
.contact-left{position:absolute;left:30px;top:70px;width:430px;font-size:20px;font-weight:500;line-height:1.2;color:var(--ink)}
.contact-line{display:flex;gap:10px;align-items:flex-start;margin-bottom:10px}
.contact-split{position:absolute;left:462px;top:72px;width:2px;height:82px;background:var(--white)}
.contact-right{position:absolute;left:520px;top:66px;color:var(--ink)}
.phone{display:flex;align-items:center;gap:12px;font-size:44px;font-weight:600;letter-spacing:1px}
.web{display:flex;align-items:center;gap:18px;font-size:22px;font-weight:600;letter-spacing:3px;margin-top:2px}
</style>
</head>
<body>
<main class="flyer">
  <div class="hero-band"></div>

  <div class="brand"><span class="brand-mark"></span>BrightKey Lending</div>

  <h1 class="headline">
    <span class="light">Want to Save</span>
    <span class="bold">More on Your</span>
    <span class="accent">Mortgage?</span>
  </h1>
  <div class="divider"></div>
  <p class="intro">Whether you're a first-time buyer or want to refinance at a lower rate, <strong>WE CAN HELP.</strong></p>

  <div class="photo-back"></div>
  <div class="photo-frame"><div class="photo" role="img" aria-label="Couple embracing in front of a two-storey house"></div></div>

  <div class="strengths">
    <div class="strength">
      <span class="badge"><svg width="32" height="32" viewBox="0 0 32 32" fill="none" stroke="#1b4f72" stroke-width="2"><circle cx="16" cy="12" r="6"/><path d="M6 28c1-6 5-9 10-9s9 3 10 9"/><path d="M9 12a7 7 0 0 1 14 0"/></svg></span>RESPONSIVE
    </div>
    <div class="strength">
      <span class="badge"><svg width="32" height="32" viewBox="0 0 32 32" fill="none" stroke="#1b4f72" stroke-width="2"><circle cx="14" cy="11" r="6"/><path d="M4 28c1-6 5-9 10-9"/><circle cx="23" cy="22" r="4"/><path d="M21 26l-1 4 3-2 3 2-1-4"/></svg></span>PROFESSIONAL
    </div>
    <div class="strength">
      <span class="badge"><svg width="32" height="32" viewBox="0 0 32 32" fill="none" stroke="#1b4f72" stroke-width="2"><path d="M6 5l1 2 2 .3-1.5 1.4.4 2L6 9.8 4.1 10.7l.4-2L3 7.3 5 7z"/><path d="M16 3l1 2 2 .3-1.5 1.4.4 2-1.9-1-1.9 1 .4-2L13 5.3l2-.3z"/><path d="M26 5l1 2 2 .3-1.5 1.4.4 2-1.9-.9-1.9.9.4-2L23 7.3l2-.3z"/><path d="M8 28V18h4l4-5 2 1-1 4h7l-1 10z"/></svg></span>EXPERIENCED
    </div>
  </div>

  <div class="showcase" role="img" aria-label="Hand holding a small model house"></div>

  <div class="features">
    <div class="feature primary">
      <div class="feature-bar"></div>
      <span class="feature-icon"><svg width="34" height="34" viewBox="0 0 34 34" fill="none" stroke="#b9d95a" stroke-width="2.4"><rect x="5" y="6" width="24" height="14" rx="2"/><path d="M12 24v6M17 24v8M22 24v6"/></svg></span>
      <span class="feature-text">LOW RATES AND CLOSING COST</span>
    </div>
    <div class="feature">
      <div class="feature-bar"></div>
      <span class="feature-icon"><svg width="34" height="34" viewBox="0 0 34 34" fill="none" stroke="#ff6b4a" stroke-width="2.6"><circle cx="17" cy="19" r="10" fill="#fff"/><path d="M17 13v6l4 3" stroke="#1b4f72"/><path d="M6 8l4-3M28 8l-4-3"/></svg></span>
      <span class="feature-text">Fast Underwrite - 24 Hours or Less</span>
    </div>
    <div class="feature">
      <div class="feature-bar"></div>
      <span class="feature-icon"><svg width="34" height="34" viewBox="0 0 34 34" fill="none" stroke="#f2c230" stroke-width="2.4"><circle cx="19" cy="20" r="8"/><path d="M19 16v8M16 18h5a2 2 0 0 1 0 4h-5"/><path d="M8 8l6 6M8 14h0" stroke="#b9d95a"/></svg></span>
      <span class="feature-text">Hundreds of products for borrowers<br>who have been declined</span>
    </div>
  </div>

  <div class="person officer">
    <div class="portrait" role="img" aria-label="Portrait of loan officer Carla Wendt"></div>
    <div class="person-info">
      <div class="person-name">Carla Wendt</div>
      <div class="person-role">Loan Officer</div>
    </div>
  </div>

  <div class="person assistant">
    <div class="portrait" role="img" aria-label="Portrait of loan officer assistant Rosa Medina"></div>
    <div class="person-info">
      <div class="person-name">Rosa Medina</div>
      <div class="person-role">Spanish Speaking</div>
      <div class="person-role">Loan Officer Assistant</div>
      <div class="person-note">"Se Habla Espanol"</div>
    </div>
  </div>

  <section class="contact">
    <div class="contact-tab">GET YOUR MORTGAGE RATE QUOTE IN<span>JUST 30 SECONDS!</span></div>
    <div class="contact-left">
      <div class="contact-line">
        <svg width="18" height="22" viewBox="0 0 18 22"><path d="M9 1a7 7 0 0 0-7 7c0 5 7 13 7 13s7-8 7-13a7 7 0 0 0-7-7z" fill="#1b4f72"/><circle cx="9" cy="8" r="2.6" fill="#b9d95a"/></svg>
        <span>1200 Maple Ridge Dr., Ste. 210<br>Riverton, GA 30100</span>
      </div>
      <div class="contact-line">
        <svg width="20" height="20" viewBox="0 0 20 20"><circle cx="10" cy="10" r="10" fill="#1b4f72"/><rect x="5" y="6.5" width="10" height="7" rx="1" fill="none" stroke="#fff" stroke-width="1.4"/><path d="M5 7l5 4 5-4" fill="none" stroke="#fff" stroke-width="1.4"/></svg>
        <span>hello@brightkeylending.com</span>
      </div>
    </div>
    <div class="contact-split"></div>
    <div class="contact-right">
      <div class="phone">
        <svg width="36" height="36" viewBox="0 0 36 36"><circle cx="18" cy="18" r="18" fill="#1b4f72"/><path d="M12 10c1-1 2-1 3 0l2 3c.5 1 0 2-1 2.5 1 2.5 3 4.5 5.5 5.5.5-1 1.5-1.5 2.5-1l3 2c1 1 1 2 0 3-2 2-5 2-9-1.5S10 13 12 10z" fill="#fff"/></svg>
        (555) 214-7730
      </div>
      <div class="web">
        <svg width="22" height="22" viewBox="0 0 22 22" fill="none" stroke="#1b4f72" stroke-width="1.8"><circle cx="11" cy="11" r="9"/><ellipse cx="11" cy="11" rx="4" ry="9"/><path d="M2 11h18"/></svg>
        www.brightkeylending.com
      </div>
    </div>
  </section>
</main>
</body>
</html>
```